Fresh, modern, fun business card for pediatric dental practice

Need a business card for fresh, modern, fun pediatric dental practice

Clean look that matches our website's font and colors

We prefer the look of curved corners on business cards

Target Market(s)

parents (mothers) of young children, professionals, mid-high class

Industry/Entity Type

Dental

Contact Information for Business Card

Maplebrook Pediatric Dentistry
482 Quarry Lane
Suite 517
Fernwick, PA 17650
717.555.0193
www.maplebrookkidsdental.example

Mei-Ran Tsai, DMD
Corinne Walbeck, DMD
(we are working on our email address, but we would like that on the card as well)

Font styles to use
Sans Serif

Requirements
Must have
• All info; we would also like to make cards for individual staff members
• colors from our website and color palatte, attatched
• use same font and design as website for branding
Nice to have
• clean, simple card that has a pop of color
• we would like to see a few designs with our tag line "where smiles get brighter"
• we are not sure if we want to have it on there or not
• we would like to see a few designs incorporating the ribbon graphic on our website where the word WELCOME is

```html
<!DOCTYPE html>
<html lang="en">
<head>
<meta charset="utf-8">
<title>Maplebrook Pediatric Dentistry – Business Card</title>
<link rel="stylesheet" href="https://fonts.googleapis.com/css2?family=Open+Sans:wght@600&family=Roboto:wght@400&family=Roboto+Condensed:wght@700&display=swap">
<style>
  :root {
    --backdrop: #2b2b2b;
    --paper: #f2f2f2;
    --sun: #efb124;
    --berry: #c72d8a;
    --ink-light: #ffffff;
  }
  * { margin: 0; padding: 0; box-sizing: border-box; }
  html, body { width: 1200px; height: 960px; overflow: hidden; }
  body { background: var(--backdrop); position: relative; font-family: "Roboto", Arial, sans-serif; }

  .card {
    position: absolute;
    width: 600px;
    height: 342px;
    border-radius: 20px;
    overflow: hidden;
  }
  .card--front { left: 314px; top: 113px; background: var(--paper); }
  .card--back { left: 311px; top: 472px; background: var(--berry); }

  .front-shapes { position: absolute; inset: 0; }

  .brand {
    position: absolute;
    left: 6px;
    top: 106px;
    width: 280px;
    text-align: center;
  }
  .brand__dot {
    display: block;
    width: 44px; height: 44px;
    margin: 0 auto 14px;
    border-radius: 50%;
    background: var(--sun);
  }
  .brand__name {
    font-family: "Open Sans", Arial, sans-serif;
    font-weight: 600;
    color: var(--sun);
    font-size: 24px;
    line-height: 1.2;
  }

  .contact {
    position: absolute;
    left: 360px;
    top: 82px;
    color: var(--ink-light);
  }
  .contact__doctors {
    font-family: "Roboto Condensed", Arial, sans-serif;
    font-weight: 700;
    font-size: 20px;
    line-height: 24px;
    margin-bottom: 8px;
  }
  .contact__address { font-size: 14px; line-height: 18px; margin-bottom: 9px; }
  .contact__line { display: flex; align-items: center; gap: 6px; font-size: 14px; line-height: 20px; }
  .contact__icon { width: 13px; height: 13px; flex: none; }

  .back-brand {
    position: absolute;
    left: 0; right: 0;
    top: 80px;
    text-align: center;
  }
  .back-brand__dot {
    display: block;
    width: 100px; height: 100px;
    margin: 0 auto 18px;
    border-radius: 50%;
    background: var(--sun);
  }
  .back-brand__name {
    font-family: "Open Sans", Arial, sans-serif;
    font-weight: 600;
    color: var(--sun);
    font-size: 28px;
  }
  .back-url {
    position: absolute;
    left: 0; right: 0;
    top: 293px;
    text-align: center;
    color: var(--ink-light);
    font-size: 13px;
    letter-spacing: 3.2px;
  }
</style>
</head>
<body>

  <section class="card card--front">
    <svg class="front-shapes" width="600" height="342" viewBox="0 0 600 342">
      <path fill="var(--sun)" d="M280,0 C330,60 335,150 318,230 C305,290 312,320 322,342 L600,342 L600,0 Z"/>
      <path fill="var(--berry)" d="M280,0 C312,70 302,180 292,240 C287,290 300,320 318,342 L322,342 C312,320 305,290 318,230 C335,150 330,60 280,0 Z"/>
      <path fill="none" stroke="#ffffff" stroke-width="2" d="M280,0 C330,60 335,150 318,230 C305,290 312,320 322,342"/>
    </svg>

    <div class="brand">
      <span class="brand__dot"></span>
      <p class="brand__name">Maplebrook<br>Pediatric Dentistry</p>
    </div>

    <div class="contact">
      <p class="contact__doctors">Mei-Ran Tsai, DMD<br>Corinne Walbeck, DMD</p>
      <p class="contact__address">Maplebrook Pediatric Dentistry<br>482 Quarry Lane<br>Suite 517<br>Fernwick, PA 17650</p>
      <p class="contact__line">
        <svg class="contact__icon" viewBox="0 0 24 24"><path fill="#fff" d="M6.6 10.8c1.4 2.8 3.8 5.1 6.6 6.6l2.2-2.2c.3-.3.7-.4 1-.2 1.1.4 2.3.6 3.6.6.6 0 1 .4 1 1V20c0 .6-.4 1-1 1C10.6 21 3 13.4 3 4c0-.6.4-1 1-1h3.5c.6 0 1 .4 1 1 0 1.3.2 2.5.6 3.6.1.3 0 .7-.2 1z"/></svg>
        717.555.0193
      </p>
      <p class="contact__line">
        <svg class="contact__icon" viewBox="0 0 24 24"><circle cx="12" cy="12" r="10" fill="none" stroke="#fff" stroke-width="2.4"/><path fill="none" stroke="#fff" stroke-width="2" d="M2 12h20M12 2c3 3 3 17 0 20M12 2c-3 3-3 17 0 20"/></svg>
        maplebrookkidsdental.example
      </p>
    </div>
  </section>

  <section class="card card--back">
    <div class="back-brand">
      <span class="back-brand__dot"></span>
      <p class="back-brand__name">Maplebrook Pediatric Dentistry</p>
    </div>
    <p class="back-url">www.maplebrookkidsdental.example</p>
  </section>

</body>
</html>
```